Maskottchen für Supplements und laborbasierte Tests im Bereich Longevity
Zielgruppe
Supplements und laborbasierte Tests im Bereich Longevity
Aufgabenstellung
Bitte an den Farben vom angehängten Logo orientieren für das Maskottchen, gerne ein Tier nehmen das für Langlebigkeit steht . Gern sehr kreativ oder auch futuristisch

```html
<!DOCTYPE html>
<html lang="de">
<head>
<meta charset="utf-8">
<title>Zeitlose Stärke – Maskottchen</title>
<link rel="stylesheet" href="https://fonts.googleapis.com/css2?family=Montserrat:ital,wght@0,400;0,500;0,700;0,800;1,700&display=swap">
<style>
  :root {
    --ink-teal: #0c4748;
    --leaf-green: #9cc31d;
    --text-dark: #1d2424;
    --paper: #ffffff;
    --mint-light: #dff2ee;
    --mint-mid: #a9dccf;
    --teal-mid: #4fb39d;
    --teal-deep: #2a8f7c;
    --shadow-mint: #c4e6df;
  }
  * { margin: 0; padding: 0; box-sizing: border-box; }
  html, body {
    width: 1200px;
    height: 674px;
    overflow: hidden;
    background: var(--paper);
  }
  .slide {
    position: relative;
    width: 1200px;
    height: 674px;
    font-family: "Montserrat", sans-serif;
    color: var(--text-dark);
  }
  .brand {
    position: absolute;
    top: 42px;
    right: 34px;
    display: flex;
    align-items: center;
    gap: 8px;
  }
  .brand-dot {
    width: 22px;
    height: 22px;
    border-radius: 50%;
    background: var(--ink-teal);
  }
  .brand-name {
    font-weight: 700;
    font-size: 25px;
    color: var(--ink-teal);
    letter-spacing: -0.2px;
  }
  .headline {
    position: absolute;
    left: 118px;
    top: 110px;
    display: flex;
    align-items: center;
    gap: 5px;
    font-weight: 800;
    font-size: 39px;
    color: var(--ink-teal);
    letter-spacing: -0.5px;
  }
  .headline-accent {
    background: var(--leaf-green);
    color: var(--paper);
    padding: 2px 14px 4px;
    border-radius: 14px;
  }
  .subheadline {
    position: absolute;
    left: 118px;
    top: 180px;
    font-weight: 700;
    font-size: 21px;
    color: var(--leaf-green);
  }
  .body-copy {
    position: absolute;
    left: 118px;
    top: 219px;
    width: 448px;
    font-weight: 500;
    font-size: 12.2px;
    line-height: 26.4px;
    hyphens: auto;
    -webkit-hyphens: auto;
  }
  .quote {
    position: absolute;
    left: 118px;
    top: 455px;
    display: flex;
    gap: 24px;
  }
  .quote-bar {
    width: 6px;
    height: 70px;
    background: linear-gradient(to bottom, var(--leaf-green), var(--ink-teal));
  }
  .quote-text {
    width: 290px;
    margin-top: -6px;
    font-style: italic;
    font-weight: 700;
    font-size: 12.2px;
    line-height: 26.4px;
  }
  .mascot {
    position: absolute;
    left: 615px;
    top: 290px;
    width: 430px;
    height: 315px;
  }
  .mascot-ground {
    position: absolute;
    left: 0;
    bottom: 0;
    width: 390px;
    height: 34px;
    border-radius: 50%;
    background: var(--shadow-mint);
  }
  .mascot-body {
    position: absolute;
    left: 12px;
    top: 0;
    width: 418px;
    height: 290px;
    border-radius: 52% 48% 40% 45% / 58% 62% 38% 42%;
    background: radial-gradient(ellipse at 38% 38%, var(--teal-mid) 0%, var(--teal-deep) 28%, var(--mint-mid) 58%, var(--mint-light) 100%);
  }
</style>
</head>
<body>
<main class="slide">
  <div class="brand">
    <span class="brand-dot"></span>
    <span class="brand-name">Vivorum</span>
  </div>

  <h1 class="headline">Zeitlose <span class="headline-accent">Stärke</span></h1>
  <h2 class="subheadline">Aus der Longevity-Forschung</h2>

  <p class="body-copy">Die Schildkröte ist das ideale Motiv für Vivorum: Sie steht wie kein anderes Tier für ein langes, gesundes Leben. Ihr ruhiger, verlässlicher Charakter vermittelt Vertrauen – ein entscheidender Faktor im Be&shy;reich Laboranalytik und Supplements. Gleichzeitig transportiert ihr futuristisch-biologischer Look den wissenschaftlichen Anspruch der Marke und schafft ein ikonisches, sympathisches Wiedererkennungs&shy;merkmal.</p>

  <blockquote class="quote">
    <span class="quote-bar"></span>
    <p class="quote-text">Langlebigkeit entsteht, wenn Ausdauer, Wissen und innere Stärke miteinander verschmelzen.</p>
  </blockquote>

  <div class="mascot" role="img" aria-label="Maskottchen: futuristische Schildkröte in Mint- und Petroltönen mit leuchtender DNA-Helix auf dem Panzer, stehend auf einem sanften Bodenschatten">
    <span class="mascot-ground" aria-hidden="true"></span>
    <span class="mascot-body" aria-hidden="true"></span>
  </div>
</main>
</body>
</html>
```